Community Management Company in need of WordPress templates for website redesign

We are a community association management company providing services to homeowner associations (HOAs), condominium associations, cooperatives, municipal utility districts, luxury high-rises and large master-planned communities within the Real Estate category.

We are looking to do a refresh of our site with newly-designed pages that are compatible with WordPress and can be uploaded to a domain with little complications.

We are interested in first having a landing page designed based on a specific audience and call to actions as described in the design brief file attached to this design project and pasted below:
Design Brief for HavenStead Website Refresh

General Details:
Company Name: HavenStead
Business Location: Carrollton, TX – HQ
Current website: www.havenstead-example.com

Overview:

We are looking to for a refresh of our site with newly-designed pages that are compatible with WordPress and can be uploaded to a domain with little complications.

Our target audience / target market:
HOA and Association Board Members, Real Estate Builders & Developers, Residents and Homeowners, Vendors, Potential Business Partners

Project scope:
Create a landing page template with the target audience of HOA Board Members who are prospects of HavenStead
The goal of the landing page is to have them fill out the proposal form by having the page take them from our “why” message to our “how” and “what” messages so they are compelled to fill out the form. The new landing page needs to drive that behavior.
Our messages will include the following

Why messages:
• Because you deserve an exceptional community
• Because you and your residents deserve an exceptional lifestyle
• Because your community matters
• Because your residents matter
• Exceptional Community. Managed
• Exceptional Lifestyle. Delivered
How/What messages:

With over 25 years of experience, HavenStead provides exceptional community management solutions with the transparency and visibility your community deserves. Our fully integrated services are provided at competitive prices with the best people, best practices, and best cloud-based and mobile app technology.

Our team is made up of the industry’s leading experts equipped to answer your questions quickly. Our team includes: certified managers, degreed and certified accountants, experienced, multi-lingual customer service representatives, technology staff and industry executives. We perform industry leading best practices, on behalf of the communities we serve, ensuring you receive the highest level support, guidance and tools to assist in performing your fiduciary duties. With our proprietary, cloud-based and mobile app technology, pertinent community information is at your fingertips. You will be empowered to manage the business affairs of your community anytime, from any device, anywhere.

Our community management services include personalized onsite management, portfolio management, full-service community maintenance services, community management for builders and property developers, and Virtual CAM (Community Association Manager) management.

Our community communication services include cloud-based board, resident, closing, and attorney portals and mobile app technology, providing the transparency and visibility into the business affairs that your community deserves. In addition, we provide several communication tools to keep homeowners and residents informed via our community website, newsletter and event services.

HavenStead, one of the largest and fastest growing community management companies, is proud to provide exceptional services to hundreds of community associations from under 50 units to over 7,000 units in Arizona, California, Colorado, Florida, Georgia, Louisiana, Nevada, North Carolina, Oregon, Texas and Washington, including homeowner associations (HOAs), condominium associations, cooperatives, luxury high-rises, municipal utility districts and large master-planned communities.

Other page elements: additional content block/placeholders for:
• Link to Service description and technology pages
• Link to Mobile Apps page
• Request a proposal form fill content block
• Find an office form fill content block and link to local page upon completion of search via zip or state
• Contact us content block with information to include phone, email, fax, etc. and link to contact us landing page

Template Elements:
Files will also be uploaded including:
• Logo
• Colors
• Sales PPT for their reference

Please see attached design brief (file #4), logos (file #2&3), colors & branding standards (file #5) and a sales PPT deck (file #1) geared towards the audience for your reference.
Updates

Reason: I am extending the deadline by one week to give everyone a chance to provide updates based on the feedback and submissions. Thank you for all of your efforts. I look forward to seeing all of your designs.

Reason: Good day everyone, We are extending our deadline by one more week; so please continue to submit your designs and revisions. We look forward to seeing your work. Regards.

Thank you for all of your submissions.  I am in the process of getting votes tallied and should have some further information Tuesday of next week.

I am currently reviewing the votes and comments from the poll and will provide feedback within the next day; so please stay tuned.

We are conducting one more round of voting for the website refresh.  Once this is complete we will contact the finalists and make a selection shortly thereafter.  Thank you again for your participation.  Please stay tuned.

We are finalizing our 2nd poll and will request revisions, if appropriate.  Thank you.

Target Market(s)

HOA Board members per the design brief

Industry/Entity Type

Communication

Requirements
Must have
• focus on a landing page first; not the homepage design
Nice to have
• Please see design brief - File #4
Should not have
• home page elements for the time being.

```html
<!DOCTYPE html>
<html lang="en">
<head>
<meta charset="utf-8">
<title>HavenStead – Landing Page</title>
<link href="https://fonts.googleapis.com/css2?family=Oxygen:wght@300;400&family=Open+Sans:wght@300;400&display=swap" rel="stylesheet">
<style>
  :root {
    --page-bg: #ffffff;
    --header-bg: #fcfcfb;
    --brand-green: #4a7a2c;
    --brand-teal: #1f6a80;
    --nav-blue: #0c6f9c;
    --heading-teal: #1b6677;
    --body-text: #555555;
    --footer-bg: #f6f6f6;
    --footer-line: #e2e2e2;
    --footer-text: #444444;
    --muted: #777777;
    --icon-grey: #666666;
  }
  * { box-sizing: border-box; margin: 0; padding: 0; }
  html, body { width: 1100px; height: 1200px; overflow: hidden; background: var(--page-bg); }
  body { font-family: "Open Sans", Arial, sans-serif; color: var(--body-text); position: relative; }

  .site-header {
    height: 112px; background: var(--header-bg); border-bottom: 1px solid #e6e6e6;
    position: relative;
  }
  .brand { position: absolute; left: 99px; top: 28px; }
  .brand-name {
    font-family: "Oxygen", Arial, sans-serif; font-size: 38px; font-weight: 400;
    color: var(--brand-green); letter-spacing: -0.5px; line-height: 1; display: flex; align-items: center; gap: 8px;
  }
  .brand-mark { width: 10px; height: 10px; background: var(--brand-teal); display: inline-block; }
  .brand-powered {
    font-size: 7px; color: var(--brand-teal); text-transform: uppercase; letter-spacing: 0.5px;
    text-align: right; margin-top: 6px;
  }
  .header-phone {
    position: absolute; right: 99px; top: 18px; display: flex; align-items: center; gap: 4px;
    font-family: "Oxygen", Arial, sans-serif; font-size: 24px; color: var(--brand-green);
  }
  .main-nav { position: absolute; right: 99px; top: 69px; display: flex; gap: 46px; }
  .main-nav a {
    font-family: "Oxygen", Arial, sans-serif; font-size: 16px; color: var(--nav-blue);
    text-decoration: none; letter-spacing: 0.2px;
  }

  .hero {
    position: relative; height: 470px;
    background: linear-gradient(180deg, #9fd0ee 0%, #d9e4e2 35%, #cfc7b8 58%, #7e9a4e 80%, #5f8236 100%);
  }
  .hero-tagline {
    position: absolute; left: 0; right: 0; top: 180px; text-align: center; color: #fff;
    font-family: "Open Sans", Arial, sans-serif; font-weight: 400; text-shadow: 0 1px 3px rgba(0,0,0,0.35);
  }
  .hero-tagline .lead { font-size: 36px; line-height: 1.1; display: block; }
  .hero-tagline .focus { font-size: 54px; line-height: 1.05; display: block; }
  .hero-dots { position: absolute; left: 0; right: 0; bottom: 14px; display: flex; justify-content: center; gap: 4px; }
  .hero-dots span { width: 14px; height: 14px; border-radius: 50%; background: #fff; }

  .welcome { padding: 34px 99px 0; text-align: center; }
  .welcome-title {
    font-family: "Oxygen", Arial, sans-serif; font-weight: 300; font-size: 34px;
    color: var(--heading-teal); margin-bottom: 8px;
  }
  .welcome p { font-size: 12px; font-weight: 300; line-height: 19px; margin-bottom: 13px; color: var(--body-text); }

  .cta-row { display: flex; justify-content: center; gap: 13px; margin-top: 19px; }
  .btn {
    width: 126px; height: 34px; border-radius: 3px; color: #fff; font-size: 13px;
    display: flex; align-items: center; justify-content: center; text-decoration: none;
    box-shadow: 0 1px 2px rgba(0,0,0,0.3);
  }
  .btn-start { background: linear-gradient(#5f8e32, #3e6a1e); }
  .btn-learn { background: linear-gradient(#1e6b80, #0d4a5c); }

  .site-footer {
    position: absolute; left: 0; right: 0; top: 1110px; bottom: 0;
    background: var(--footer-bg); border-top: 1px solid var(--footer-line);
  }
  .footer-nav { position: absolute; left: 99px; top: 30px; font-size: 15px; color: var(--footer-text); }
  .footer-nav a { color: var(--footer-text); text-decoration: none; }
  .footer-nav .sep { margin: 0 8px; }
  .copyright { position: absolute; left: 99px; top: 64px; font-size: 12px; color: var(--muted); }
  .social { position: absolute; right: 99px; top: 24px; display: flex; gap: 6px; }
  .social span { width: 20px; height: 20px; border-radius: 50%; background: var(--icon-grey); }
</style>
</head>
<body>
  <header class="site-header">
    <div class="brand">
      <div class="brand-name"><span class="brand-mark"></span>HavenStead</div>
      <div class="brand-powered">powered by NexaLink</div>
    </div>
    <div class="header-phone">
      <svg width="20" height="20" viewBox="0 0 24 24" aria-hidden="true"><path fill="#c9c9c9" d="M6.6 10.8a15.1 15.1 0 006.6 6.6l2.2-2.2c.3-.3.7-.4 1-.2 1.1.4 2.3.6 3.6.6.6 0 1 .4 1 1V20c0 .6-.4 1-1 1A17 17 0 013 4c0-.6.4-1 1-1h3.5c.6 0 1 .4 1 1 0 1.3.2 2.5.6 3.6.1.3 0 .7-.2 1l-2.3 2.2z"/></svg>
      555.014.2870
    </div>
    <nav class="main-nav">
      <a href="#">HOME</a><a href="#">ABOUT</a><a href="#">FEATURES</a><a href="#">BLOG</a><a href="#">CONTACT</a>
    </nav>
  </header>

  <section class="hero" role="img" aria-label="Photo of a sunny tiled-roof villa with a green lawn and garden plants">
    <h1 class="hero-tagline"><span class="lead">Because you deserve an</span><span class="focus">Exceptional Community</span></h1>
    <div class="hero-dots"><span></span><span></span><span></span></div>
  </section>

  <main class="welcome">
    <h2 class="welcome-title">Welcome to Our Website Mainpage</h2>
    <p>With over 25 years of experience, HavenStead provides exceptional community management solutions with the transparency and visibility your community deserves. Our fully integrated services are provided at competitive prices with the best people, best practices, and best cloudbased and mobile app technology. Our team is made up of the industry’s leading experts equipped to answer your questions quickly.</p>
    <p>Our team includes: certified managers, degreed and certified accountants, experienced, multi lingual customer service representatives, technology staff and industry executives. We perform industry leading best practices, on behalf of the communities we serve, ensuring you receive the highest level support, guidance and tools to assist in performing your fiduciary duties. With our proprietary, cloudbased and mobile app technology, pertinent community information is at your fingertips. You will be empowered to manage the business affairs of your community anytime, from any device, anywhere.</p>
    <p>Our community management services include personalized onsite management, portfolio management, fullservice community maintenance services, community management for builders and property developers, and Virtual CAM (Community Association Manager) management.</p>
    <p>Our community communication services include cloudbased board, resident, closing, and attorney portals and mobile app technology, providing the transparency and visibility into the business affairs that your community deserves. In addition, we provide several communication tools to keep homeowners and residents informed via our community website, newsletter and event services.</p>
    <p>HavenStead, one of the largest and fastest growing community management companies, is proud to provide exceptional services to hundreds of community associations from under 50 units to over 7,000 units in Arizona, California, Colorado, Florida, Georgia, Louisiana, Nevada, North Carolina, Oregon, Texas and Washington, including homeowner associations (HOAs), condominium associations, cooperatives, luxury highrises, municipal utility districts and large masterplanned communities.</p>
    <div class="cta-row">
      <a class="btn btn-start" href="#">GET STARTED</a>
      <a class="btn btn-learn" href="#">LEARN MORE</a>
    </div>
  </main>

  <footer class="site-footer">
    <nav class="footer-nav">
      <a href="#">Home</a><span class="sep">|</span><a href="#">About</a><span class="sep">|</span><a href="#">Services</a><span class="sep">|</span><a href="#">Support</a><span class="sep">|</span><a href="#">Contact</a>
    </nav>
    <p class="copyright">Copyright © 2014 Company Name.&nbsp; All right reserved</p>
    <div class="social" aria-label="Social links"><span></span><span></span><span></span></div>
  </footer>
</body>
</html>
```